Building company buisness cards

We are looking for a sharp modern new look for our business cards.
We are a New Zealand based company that specialises in house and land packages.
We have attached a photo of the current logo and would like to see if it can be improved somehow if needed.
We are open to any colours but we have chosen green at this stage.
Feel free to change the font and make the logo smarter looking.
Play with the colours and see what looks best.

We want a card that looks so good know one will want to throw it away!

Target Market(s)

Home buyers

Industry/Entity Type

Building

Contact Information for Business Card

Derek Tolvane
0217394062
dtolvane@quillmarkhomesteads.co.nz
quillmarkhomesteads.co.nz

Font styles to use
Serif
Sans Serif

Colors

Designer to choose colors to be used in the design.

Requirements
Must have
• Logo and company name on one side, details on the other side
Nice to have
• Color codes for the original green are HEX #4a8028, RGB(74,128,40), CMYK(42,0,69,50)
• Round corners, Raised and/or spot UV

```html
<!DOCTYPE html>
<html lang="en">
<head>
<meta charset="utf-8">
<title>Quillmark Homesteads business cards</title>
<link href="https://fonts.googleapis.com/css2?family=Montserrat:wght@400;600;800&display=swap" rel="stylesheet">
<style>
  :root {
    --brand-green: #4a8028;
    --swoosh-grey: #a9a9a9;
    --card-white: #ffffff;
    --ink: #3a3a3a;
    --backdrop: #262626;
  }
  html, body {
    margin: 0;
    padding: 0;
    width: 1200px;
    height: 897px;
    overflow: hidden;
    background: var(--backdrop);
    font-family: "Montserrat", Arial, sans-serif;
  }
  .stage {
    position: relative;
    width: 1200px;
    height: 897px;
  }
  .card {
    position: absolute;
    left: 303px;
    width: 594px;
    height: 338px;
    border-radius: 19px;
    overflow: hidden;
    box-shadow: 0 6px 14px rgba(0,0,0,0.45);
  }
  .card--front { top: 92px; background: var(--card-white); }
  .card--back { top: 469px; background: var(--brand-green); }

  .holder {
    position: absolute;
    left: 35px;
    top: 116px;
  }
  .holder__name {
    margin: 0;
    font-weight: 600;
    font-size: 21px;
    line-height: 1;
    color: var(--brand-green);
  }
  .holder__role {
    margin: 6px 0 0;
    font-weight: 400;
    font-size: 15px;
    line-height: 1;
    color: var(--ink);
  }

  .wordmark {
    position: absolute;
    text-align: center;
    font-weight: 800;
    line-height: 1;
    letter-spacing: -0.5px;
  }
  .wordmark span { display: block; }
  .wordmark--front {
    right: 47px;
    top: 92px;
    width: 270px;
    color: var(--brand-green);
  }
  .wordmark--front .wordmark__top { font-size: 25px; }
  .wordmark--front .wordmark__bottom { font-size: 31px; margin-top: 3px; }

  .wordmark--back {
    left: 0;
    right: 0;
    top: 122px;
    color: var(--card-white);
  }
  .wordmark--back .wordmark__top { font-size: 40px; }
  .wordmark--back .wordmark__bottom { font-size: 50px; margin-top: 6px; }

  .divider {
    position: absolute;
    left: 35px;
    top: 189px;
    width: 521px;
    height: 2px;
    background: var(--brand-green);
  }

  .contacts {
    position: absolute;
    left: 35px;
    top: 220px;
    margin: 0;
    padding: 0;
    list-style: none;
    font-size: 14px;
    color: var(--ink);
  }
  .contacts li {
    display: flex;
    align-items: center;
    height: 19px;
  }
  .contacts svg {
    width: 10px;
    height: 10px;
    margin-right: 6px;
    flex: none;
  }

  .swoosh {
    position: absolute;
    left: 0;
    bottom: 0;
    width: 594px;
    height: 338px;
  }
</style>
</head>
<body>
<div class="stage">

  <section class="card card--front">
    <div class="holder">
      <p class="holder__name">Derek Tolvane</p>
      <p class="holder__role">Founder</p>
    </div>

    <div class="wordmark wordmark--front">
      <span class="wordmark__top">quillmark</span>
      <span class="wordmark__bottom">homesteads.</span>
    </div>

    <div class="divider"></div>

    <ul class="contacts">
      <li>
        <svg viewBox="0 0 10 10" aria-hidden="true"><path d="M2.2 0.8l1.5 1.6-0.8 1.3c0.5 1.3 1.4 2.2 2.6 2.8l1.3-0.8 1.6 1.5-0.9 1.6C4.6 8.6 1.3 5.3 0.6 1.7z" fill="var(--brand-green)"/></svg>
        0217394062
      </li>
      <li>
        <svg viewBox="0 0 10 10" aria-hidden="true"><rect x="0.8" y="2" width="8.4" height="6" fill="none" stroke="var(--brand-green)" stroke-width="1"/><path d="M0.8 2l4.2 3.4L9.2 2" fill="none" stroke="var(--brand-green)" stroke-width="1"/></svg>
        dtolvane@quillmarkhomesteads.co.nz
      </li>
      <li>
        <svg viewBox="0 0 10 10" aria-hidden="true"><g fill="none" stroke="var(--brand-green)" stroke-width="0.9"><circle cx="5" cy="5" r="4.2"/><ellipse cx="5" cy="5" rx="1.8" ry="4.2"/><path d="M0.8 5h8.4M1.5 2.8h7M1.5 7.2h7"/></g></svg>
        quillmarkhomesteads.co.nz
      </li>
    </ul>

    <svg class="swoosh" viewBox="0 0 594 338" aria-hidden="true">
      <path d="M73 338 C230 290 420 285 594 296 L594 338 Z" fill="var(--swoosh-grey)"/>
      <path d="M160 338 C300 306 460 300 594 306 L594 338 Z" fill="var(--card-white)"/>
      <path d="M177 338 C310 310 465 304 594 309 L594 338 Z" fill="var(--brand-green)"/>
    </svg>
  </section>

  <section class="card card--back">
    <div class="wordmark wordmark--back">
      <span class="wordmark__top">quillmark</span>
      <span class="wordmark__bottom">homesteads.</span>
    </div>
  </section>

</div>
</body>
</html>
```